Business Card Design

Business Card for professional consulting firm working with large financial institutions.

Target Market(s)

Executive buyers

Industry/Entity Type

Banking

Contact Information for Business Card

Mild creativity wanted. Not boring, but do elaborate artwork.

Font styles to use
Serif
Sans Serif

Colors

Designer to choose colors to be used in the design.

Requirements
Must have
• Standard business card features - company name, individual name, telephone, website, email, locations.
Nice to have
• Two colors
Should not have
• too many colors, fancy printing, cartoons.

```html
<!DOCTYPE html>
<html lang="en">
<head>
<meta charset="utf-8">
<title>k7advisory business card</title>
<link href="https://fonts.googleapis.com/css2?family=Roboto:wght@400;700&family=Roboto+Condensed:wght@700&display=swap" rel="stylesheet">
<style>
  :root {
    --backdrop: #a8a8a8;
    --card-light: #f4f4f4;
    --card-dark: #000000;
    --ink: #111111;
    --ink-soft: #3a3a3a;
    --muted: #a6a6a6;
    --rule: #6a6a6a;
    --band-grey: #b9b9b9;
    --white: #ffffff;
  }
  html, body {
    margin: 0;
    padding: 0;
    width: 1200px;
    height: 960px;
    overflow: hidden;
    background: var(--backdrop);
    font-family: "Roboto", Arial, sans-serif;
  }
  .canvas { position: relative; width: 1200px; height: 960px; }

  .card { position: absolute; width: 600px; height: 343px; overflow: hidden; }
  .card-front { left: 322px; top: 108px; background: var(--card-light); }
  .card-back { left: 320px; top: 493px; background: var(--card-dark); }

  .brand-name {
    position: absolute;
    font-family: "Roboto", Arial, sans-serif;
    font-weight: 400;
    white-space: nowrap;
  }
  .card-front .brand-name { right: 40px; top: 56px; font-size: 30px; color: var(--ink); }
  .card-back .brand-name { left: 0; right: 0; top: 142px; text-align: center; font-size: 36px; color: var(--white); }

  .person-name {
    position: absolute; left: 33px; top: 186px; margin: 0;
    font-family: "Roboto Condensed", "Roboto", sans-serif;
    font-weight: 700; font-size: 23px; color: var(--ink); letter-spacing: 0.2px;
  }
  .person-title {
    position: absolute; left: 33px; top: 214px;
    font-size: 14px; font-weight: 700; color: var(--muted);
  }
  .divider {
    position: absolute; left: 33px; top: 241px; width: 532px; height: 1px; background: var(--rule);
  }
  .contact-list {
    position: absolute; left: 33px; top: 253px; margin: 0; padding: 0; list-style: none;
    font-size: 14px; color: var(--ink-soft); line-height: 19px;
  }
  .contact-list li { display: flex; align-items: center; gap: 8px; }
  .contact-list svg { width: 13px; height: 13px; fill: var(--ink); flex: none; }
  .address {
    position: absolute; right: 32px; top: 254px; margin: 0; text-align: right;
    font-style: normal; font-size: 14px; color: var(--ink-soft); line-height: 18.5px;
  }
  .bottom-band { position: absolute; left: 0; bottom: 0; width: 600px; height: 13px; }

  .web-address {
    position: absolute; left: 0; right: 0; top: 281px; text-align: center;
    font-size: 14px; color: var(--white); letter-spacing: 5.2px;
  }
</style>
</head>
<body>
<main class="canvas">
  <section class="card card-front" aria-label="Business card front">
    <div class="brand-name">k7advisory</div>
    <h1 class="person-name">LAURA BENNETT</h1>
    <div class="person-title">CEO/FOUNDER</div>
    <div class="divider"></div>
    <ul class="contact-list">
      <li>
        <svg viewBox="0 0 24 24" aria-hidden="true"><path d="M6.6 10.8a15.1 15.1 0 0 0 6.6 6.6l2.2-2.2c.3-.3.7-.4 1-.2 1.1.4 2.3.6 3.6.6.6 0 1 .4 1 1V20c0 .6-.4 1-1 1C10.6 21 3 13.4 3 4c0-.6.4-1 1-1h3.5c.6 0 1 .4 1 1 0 1.3.2 2.5.6 3.6.1.3 0 .7-.2 1z"/></svg>
        555 210 4861
      </li>
      <li>
        <svg viewBox="0 0 24 24" aria-hidden="true"><path d="M2 5h20v14H2zm2 2v.5l8 5 8-5V7zm0 3v7h16v-7l-8 5z"/></svg>
        info@k7advisory.com
      </li>
      <li>
        <svg viewBox="0 0 24 24" aria-hidden="true"><circle cx="12" cy="12" r="10"/><path d="M7 7c2 0 3 1 3 3s-2 2-2 4 1 3 1 5c-3-1-5-4-5-7 0-2 1-4 3-5zm8-2c2 1 4 3 4 6-1 0-2 0-3 1s0 3-1 4-2 0-2-2 1-2 1-4-1-3 1-5z" fill="#f4f4f4"/></svg>
        www.k7advisory.com
      </li>
    </ul>
    <address class="address">
      k7advisory<br>
      2140 Birchwood Avenue<br>
      Harbor Point, Alaska 99512
    </address>
    <svg class="bottom-band" viewBox="0 0 600 13" preserveAspectRatio="none" aria-hidden="true">
      <polygon points="0,0 320,0 316,13 0,13" fill="var(--card-dark)"/>
      <polygon points="324,0 600,0 600,13 320,13" fill="var(--band-grey)"/>
    </svg>
  </section>

  <section class="card card-back" aria-label="Business card back">
    <div class="brand-name">k7advisory</div>
    <div class="web-address">www.k7advisory.com</div>
  </section>
</main>
</body>
</html>
```